New career and executive coaching business needs a business card design including logo

Company name: 'Bramblefield Growth Partners.' The aim of my coaching engagements is to help people improve their communication in the workplace and achieve their career goals. The process involves working with individuals to help them uncover their strengths and talents, then leverage those to improve their working lives. The Tarwick Inventory is the starting point to the process. I am after an exciting and interesting business card design (including logo)which is professional yet will still get people's attention.

Industry/Entity Type

Business

Contact Information for Business Card

Name: Malcolm Dervaney
Position: Owner
Address: 58 Quorrin Ct, Elmbridge Vic 3190
Phone: 0418923047
Website: bramblefieldgrowth.com.au
Email: malcolm@bgp.com.au

Colors
33a6d7
00a990
0355a3
3176b5

Requirements
Must have
• logo

```html
<!DOCTYPE html>
<html lang="en">
<head>
<meta charset="utf-8">
<title>Bramblefield Growth Partners – Business Card</title>
<link href="https://fonts.googleapis.com/css2?family=Oswald:wght@500;600&family=Open+Sans:wght@400;600&display=swap" rel="stylesheet">
<style>
  :root {
    --backdrop: #a3a3a3;
    --card-black: #141414;
    --card-edge: #1e1e1e;
    --white: #ffffff;
    --soft-grey: #cfcfcf;
    --teal: #00a990;
    --sky: #33a6d7;
    --royal: #0355a3;
    --steel: #3176b5;
  }
  * { margin: 0; padding: 0; box-sizing: border-box; }
  html, body {
    width: 1200px;
    height: 900px;
    overflow: hidden;
  }
  body {
    background: var(--backdrop);
    display: flex;
    flex-direction: column;
    align-items: center;
    justify-content: center;
    gap: 44px;
  }
  .card {
    position: relative;
    width: 660px;
    height: 378px;
    background: radial-gradient(ellipse at 50% 40%, var(--card-edge) 0%, var(--card-black) 70%);
    box-shadow: 0 10px 24px rgba(0,0,0,0.25);
    overflow: hidden;
  }

  /* Front */
  .card-front {
    display: flex;
    flex-direction: column;
    align-items: center;
    justify-content: center;
  }
  .front-wordmark {
    font-family: "Oswald", sans-serif;
    font-weight: 600;
    color: var(--white);
    text-transform: uppercase;
    text-align: center;
    line-height: 1.05;
  }
  .front-wordmark .line-main {
    display: block;
    font-size: 62px;
    letter-spacing: 2px;
  }
  .front-wordmark .line-sub {
    display: block;
    font-size: 27px;
    letter-spacing: 1px;
  }

  /* Back */
  .card-back { font-family: "Open Sans", sans-serif; }
  .holder {
    position: absolute;
    left: 60px;
    top: 112px;
  }
  .holder-name {
    color: var(--teal);
    font-weight: 600;
    font-size: 21px;
    line-height: 1.1;
  }
  .holder-role {
    color: var(--soft-grey);
    font-size: 15px;
  }
  .brand {
    position: absolute;
    left: 290px;
    top: 86px;
    display: flex;
    align-items: center;
    gap: 16px;
  }
  .brand-dot {
    width: 62px;
    height: 62px;
    border-radius: 50%;
    background: var(--steel);
    flex: none;
  }
  .brand-name {
    font-family: "Oswald", sans-serif;
    font-weight: 600;
    color: var(--sky);
    text-transform: uppercase;
    font-size: 25px;
    line-height: 1.05;
    letter-spacing: 0.5px;
  }
  .contact {
    position: absolute;
    right: 40px;
    top: 222px;
    text-align: right;
    color: var(--white);
    font-size: 17px;
    line-height: 1.3;
  }
  .contact address {
    font-style: normal;
    margin-bottom: 10px;
  }
  .contact-row {
    display: flex;
    justify-content: flex-end;
    align-items: center;
    gap: 12px;
  }
  .contact-row svg {
    width: 14px;
    height: 14px;
    fill: var(--teal);
    flex: none;
  }
</style>
</head>
<body>

  <section class="card card-front" aria-label="Card front">
    <h1 class="front-wordmark">
      <span class="line-main">Bramblefield</span>
      <span class="line-sub">Growth Partners</span>
    </h1>
  </section>

  <section class="card card-back" aria-label="Card back">
    <div class="holder">
      <p class="holder-name">Malcolm Dervaney</p>
      <p class="holder-role">Owner</p>
    </div>

    <div class="brand">
      <span class="brand-dot"></span>
      <p class="brand-name">Bramblefield<br>Growth Partners</p>
    </div>

    <div class="contact">
      <address>58 Quorrin Ct, Elmbridge<br>Vic 3190</address>
      <p class="contact-row">0418923047
        <svg viewBox="0 0 24 24" aria-hidden="true"><path d="M6.6 10.8a15.1 15.1 0 0 0 6.6 6.6l2.2-2.2a1 1 0 0 1 1-.25 11.4 11.4 0 0 0 3.6.57 1 1 0 0 1 1 1V20a1 1 0 0 1-1 1A17 17 0 0 1 3 4a1 1 0 0 1 1-1h3.5a1 1 0 0 1 1 1c0 1.25.2 2.45.57 3.57a1 1 0 0 1-.25 1z"/></svg>
      </p>
      <p class="contact-row">malcolm@bgp.com.au
        <svg viewBox="0 0 24 24" aria-hidden="true"><path d="M2 5h20v14H2z M3.5 6.5 12 13l8.5-6.5" fill="var(--teal)"/><path d="M3.5 6.5 12 13l8.5-6.5" fill="none" stroke="var(--card-black)" stroke-width="1.8"/></svg>
      </p>
      <p class="contact-row">bramblefieldgrowth.com.au
        <svg viewBox="0 0 24 24" aria-hidden="true"><circle cx="12" cy="12" r="10"/><path d="M2 12h20M12 2c3 3 3 17 0 20M12 2c-3 3-3 17 0 20" fill="none" stroke="var(--card-black)" stroke-width="1.6"/></svg>
      </p>
    </div>
  </section>

</body>
</html>
```